Website for Brisk Morning Rambles who develops hiking guides for easy to moderate hikes of up to 4 hours

Website for a company who creates hiking guides for State Parks and other tourist destinations. Looking for the ability to showcase various hiking destinations, our hiking guides, product favorites and blog with the ability to sell our hiking guides via the website shopping cart. Should feature photos from our hiking guides with the the ability to include photo thumbnails that can be expanded.

We need the ability to self manage the website - including ability to self update, add pages, graphics, etc.

While we want to have high quality photos we still want the pages to load quickly

Target Market(s)

People who enjoy nature and like to walk or hike for up to half a day on trails in a specific destination.
Adventure travelers who loves nature and the outdoors

Industry/Entity Type

Travel

Font styles to use
Sans Serif

Colors

Designer to choose colors to be used in the design.

Requirements
Must have
• We are looking for a fully operational WIX design for www.briskmorningrambles.example that has the following:
• 1. Menus - We want the ability to have multiple drop-down menus.
• 2. E-commerce – the ability to accept orders for books that we publish.
• 3. A form that can be filled out online to provide feedback on our hiking guides. (We will give the fields that need to be filled out.)
• 4. Pictures - Incorporates Professional Pictures– thumbnails that can be clicked to be larger, and pictures included with copy.
• 5. Logo – Our logo can be provided.
• 6. Domain Name - We already have the domain name briskmorningrambles.example
• 7. We want to be able to take your design and do our own changes via WIX.
• 8. The home page should have the ability to have scrolling photos – up to 10 images that can be easily updated.
• 9. Password protected pages that can only be accessed by a password.
• 10. We have a color palate that should be used for the site design
• 11. Six (6) major tabs
• #1 Home Page – Scrolling photos, general overview, hiking guide summary, other
• # 2 Destinations – Summary of all guides published, with sub-pages on each guide
• #3 Favorite products
• # 4 Blog – Blog index and all blogs
• #5 Photography
• #6 Contact us – form for feedback, links to other sites etc.
• We also need the ability to link to our Facebook and Instagram Accounts.
• Photos included as an example for our Home page.
• Please use the colors in our color palette provided as an attachment
Nice to have
• Examples of website designs we like as a reference
• https://www.roamingtheparkers.example
• https://www.torvalegrove.example/index.php
Should not have
• Colors that do not align with our color palette that is included as an attachment.

```html
<!DOCTYPE html>
<html lang="en">
<head>
<meta charset="utf-8">
<title>Brisk Morning Rambles</title>
<link href="https://fonts.googleapis.com/css2?family=Lato:wght@400;700;900&display=swap" rel="stylesheet">
<style>
:root{
  --blue:#2d5a9a;
  --blue-light:#5b86c8;
  --rust:#7a2a20;
  --orange:#e0963a;
  --ink:#3a3a3a;
  --white:#ffffff;
  --rule:#d6d6d6;
}
*{margin:0;padding:0;box-sizing:border-box}
html,body{width:1200px;height:2466px;overflow:hidden;background:var(--white)}
body{font-family:'Lato',sans-serif;color:var(--ink);position:relative}
.abs{position:absolute}

/* header */
.brand{left:75px;top:36px;font-weight:900;font-size:26px;color:var(--blue);line-height:1.05;display:flex;align-items:center;gap:10px}
.brand-dot{width:26px;height:26px;background:var(--orange)}
.email{left:587px;top:40px;width:359px;height:39px;border:1px solid #9a9a9a;font-size:14px;padding:11px 14px;color:#555}
.subscribe{left:960px;top:40px;width:166px;height:39px;background:var(--blue);color:var(--white);font-size:14px;font-weight:700;text-align:center;line-height:39px;letter-spacing:.3px}

.nav{left:0;top:115px;width:1200px;height:57px;background:var(--rust)}
.nav ul{list-style:none;display:flex;gap:37px;position:absolute;left:75px;top:21px}
.nav li,.cart{color:var(--white);font-size:14px;font-weight:700;letter-spacing:.2px}
.cart{position:absolute;right:74px;top:21px;display:flex;align-items:center;gap:8px}

.band{left:0;top:172px;width:1200px;height:311px;background:var(--orange)}

/* hero */
.hero-panel{left:75px;top:193px;width:359px;height:496px;background:var(--blue);color:var(--white);padding:118px 28px 0}
.hero-panel h1{font-size:46px;font-weight:900;line-height:.95;margin-bottom:16px}
.hero-panel p{font-size:19px;font-weight:700;line-height:1.45;padding-left:3px}
.btn{display:inline-block;background:var(--orange);color:var(--white);font-size:15px;font-weight:700;width:163px;height:45px;line-height:45px;text-align:center}
.hero-panel .btn{margin:26px 0 0 7px}
.hero-photo{left:434px;top:193px;width:692px;height:496px;background:linear-gradient(180deg,#2b62b8 0%,#6aa0d8 45%,#c9924a 60%,#8a6330 100%)}

.feature{top:689px;width:526px;height:403px;color:var(--white);padding:52px 34px 0}
.feature.welcome{left:75px;background:linear-gradient(160deg,#6e2a16 0%,#9a3c1c 45%,#3d1a10 100%)}
.feature.favorites{left:600px;background:linear-gradient(160deg,#1e3a22 0%,#3f5a2c 45%,#1c2430 100%);padding-left:29px}
.feature h2{font-size:34px;font-weight:900;line-height:1.15;margin-bottom:28px}
.feature p{font-size:17.5px;line-height:1.6;margin-bottom:36px}

/* sections */
.section-title{left:0;width:1200px;text-align:center;font-size:27px;font-weight:700;color:#3b3b3b;letter-spacing:.3px}
.thumb{top:1208px;width:242px;height:157px}
.caption{width:242px;text-align:center;font-size:16.5px;font-weight:700;color:var(--blue)}
.price{width:242px;text-align:center;font-size:16.5px;color:#c7502a}
.rule{left:75px;top:1448px;width:1051px;height:1px;background:var(--rule)}
.arrow{width:16px;height:24px}
.book{top:1535px;width:130px;height:188px;background:linear-gradient(180deg,#f3f3f3 0%,#f3f3f3 32%,#8fb1d8 45%,#5b7a4a 100%);box-shadow:4px 4px 8px rgba(0,0,0,.25)}

/* blog */
.blog{left:0;top:1828px;width:1200px;height:297px;background:var(--blue);color:var(--white)}
.blog .section-title{color:var(--white);top:52px}
.post{top:114px;width:330px;text-align:center}
.post h3{font-size:16.5px;font-weight:700;color:var(--orange);margin-bottom:12px}
.post p{font-size:14.5px;line-height:1.75}
.post time{display:block;font-size:11.5px;font-weight:700;margin-top:14px}

/* footer */
.foot-brand{left:75px;top:2262px;font-size:30px;font-weight:900;color:var(--blue);display:flex;align-items:center;gap:10px;width:200px;line-height:1.05}
.foot-col{top:2172px}
.foot-col h4{font-size:16.5px;font-weight:700;color:var(--blue);margin-bottom:6px}
.foot-col li{list-style:none;font-size:13.5px;line-height:26.8px;color:#333}
.social{display:flex;gap:14px;margin-top:14px}
.social span{width:22px;height:22px;border:2px solid #555;border-radius:50%}
.legal{left:0;top:2412px;width:1200px;height:54px;background:var(--blue-light);color:var(--white);font-size:13px;padding:25px 0 0 76px}
</style>
</head>
<body>

<header>
  <div class="abs brand"><span class="brand-dot"></span><span>Brisk Morning<br>Rambles</span></div>
  <div class="abs email">Email Address</div>
  <div class="abs subscribe">SUBSCRIBE NOW</div>
</header>

<nav class="abs nav">
  <ul>
    <li>HOME</li><li>DESTINATIONS</li><li>FAVORITE PRODUCTS</li><li>BLOG</li><li>PHOTOGRAPHY</li><li>CONTACT US</li>
  </ul>
  <div class="cart">
    <svg width="14" height="12" viewBox="0 0 14 12"><path d="M0 1h2.5l2 7h7l2-5H4" fill="none" stroke="#fff" stroke-width="1.8"/><circle cx="5.5" cy="10.5" r="1.2" fill="#fff"/><circle cx="10.5" cy="10.5" r="1.2" fill="#fff"/></svg>
    CART (0)
  </div>
</nav>

<div class="abs band"></div>

<section>
  <div class="abs hero-panel">
    <h1>Brisk Morning<br>Rambles</h1>
    <p>We are a company who creates hiking guides for State Parks and other tourist destinations.</p>
    <span class="btn">READ MORE</span>
  </div>
  <div class="abs hero-photo" role="img" aria-label="Mushroom-shaped sandstone rock formation under a blue sky in a desert park"></div>

  <div class="abs feature welcome" role="img" aria-label="Hiker overlooking red desert mountains at sunset">
    <h2>WELCOME TO<br>BRISK MORNING RAMBLES</h2>
    <p>Donec sit amet massa in dolor posuere feugiat.<br>Integer imperdiet orci sit amet sapien vehicula facilisis.<br>Cras consequat aliquam nibh, eget porttitor eros<br>congue id. Cras sodales ipsum eget justo<br>posuere sagittis.</p>
    <span class="btn">READ MORE</span>
  </div>
  <div class="abs feature favorites" role="img" aria-label="Two hikers resting outdoors looking at a phone">
    <h2>PRODUCT<br>FAVORITES</h2>
    <p>Donec sit amet massa in dolor posuere feugiat.<br>Integer imperdiet orci sit amet sapien vehicula facilisis.<br>Cras consequat aliquam nibh, eget porttitor eros<br>congue id. Cras sodales ipsum eget justo<br>posuere sagittis.</p>
    <span class="btn">READ MORE</span>
  </div>
</section>

<section>
  <h2 class="abs section-title" style="top:1148px">HIKING DESTINATIONS</h2>
  <svg class="abs arrow" style="left:47px;top:1275px" viewBox="0 0 16 24"><path d="M12 3 4 12l8 9" fill="none" stroke="#444" stroke-width="3"/></svg>
  <svg class="abs arrow" style="left:1138px;top:1275px" viewBox="0 0 16 24"><path d="M4 3l8 9-8 9" fill="none" stroke="#444" stroke-width="3"/></svg>

  <div class="abs thumb" style="left:75px;background:linear-gradient(180deg,#2f66c0 0%,#7ea6d8 45%,#6a6040 60%,#4a4a38 100%)" role="img" aria-label="Stone park entrance sign with desert hills"></div>
  <div class="abs thumb" style="left:344px;background:linear-gradient(135deg,#d8d8d0 0%,#f3e2b8 40%,#b07a3a 75%,#5a4030 100%)" role="img" aria-label="Hikers climbing rocks at sunrise"></div>
  <div class="abs thumb" style="left:615px;background:linear-gradient(180deg,#2c6ad0 0%,#9cc4ea 40%,#6a9a3a 65%,#3f6a28 100%)" role="img" aria-label="Hiker with poles on a green mountain trail"></div>
  <div class="abs thumb" style="left:884px;background:linear-gradient(180deg,#c8d6e2 0%,#9db4c8 50%,#5f7890 100%)" role="img" aria-label="Backpacker standing on a rock above misty mountains"></div>

  <div class="abs caption" style="left:75px;top:1381px">DONEC SIT AMET</div>
  <div class="abs caption" style="left:344px;top:1381px">DONEC SIT AMET</div>
  <div class="abs caption" style="left:615px;top:1381px">DONEC SIT AMET</div>
  <div class="abs caption" style="left:884px;top:1381px">DONEC SIT AMET</div>

  <div class="abs rule"></div>
</section>

<section>
  <h2 class="abs section-title" style="top:1480px">HIKING GUIDES</h2>
  <svg class="abs arrow" style="left:47px;top:1622px" viewBox="0 0 16 24"><path d="M12 3 4 12l8 9" fill="none" stroke="#444" stroke-width="3"/></svg>
  <svg class="abs arrow" style="left:1138px;top:1622px" viewBox="0 0 16 24"><path d="M4 3l8 9-8 9" fill="none" stroke="#444" stroke-width="3"/></svg>

  <div class="abs book" style="left:131px" role="img" aria-label="Mountain hiking guide book cover"></div>
  <div class="abs book" style="left:400px" role="img" aria-label="Mountain hiking guide book cover"></div>
  <div class="abs book" style="left:671px" role="img" aria-label="Mountain hiking guide book cover"></div>
  <div class="abs book" style="left:940px" role="img" aria-label="Mountain hiking guide book cover"></div>

  <div class="abs caption" style="left:75px;top:1743px">DONEC SIT AMET</div>
  <div class="abs caption" style="left:344px;top:1743px">DONEC SIT AMET</div>
  <div class="abs caption" style="left:615px;top:1743px">DONEC SIT AMET</div>
  <div class="abs caption" style="left:884px;top:1743px">DONEC SIT AMET</div>
  <div class="abs price" style="left:75px;top:1768px">$5.99</div>
  <div class="abs price" style="left:344px;top:1768px">$5.99</div>
  <div class="abs price" style="left:615px;top:1768px">$5.99</div>
  <div class="abs price" style="left:884px;top:1768px">$5.99</div>
</section>

<section class="abs blog">
  <h2 class="abs section-title">BLOG POSTS</h2>
  <article class="abs post" style="left:75px"><h3>DONEC SIT AMET MASSA</h3><p>Aenean eget velit eu mauris sollicitudin luctus vel in orci. Quisque fringilla vehicula diam, eget congue urna rutrum egestas.</p><time>JULY 22, 2019</time></article>
  <article class="abs post" style="left:436px"><h3>DONEC SIT AMET MASSA</h3><p>Aenean eget velit eu mauris sollicitudin luctus vel in orci. Quisque fringilla vehicula diam, eget congue urna rutrum egestas.</p><time>JULY 22, 2019</time></article>
  <article class="abs post" style="left:795px"><h3>DONEC SIT AMET MASSA</h3><p>Aenean eget velit eu mauris sollicitudin luctus vel in orci. Quisque fringilla vehicula diam, eget congue urna rutrum egestas.</p><time>JULY 22, 2019</time></article>
</section>

<footer>
  <div class="abs foot-brand"><span class="brand-dot" style="width:30px;height:30px;flex:none"></span><span>Brisk Morning Rambles</span></div>
  <div class="abs foot-col" style="left:301px"><h4>SITE MAP</h4><ul><li>Home</li><li>Destinations</li><li>Favorite products</li><li>Blog</li><li>Photography</li><li>Contact us</li></ul></div>
  <div class="abs foot-col" style="left:498px"><h4>HIKING GUIDES</h4><ul><li>Aenean eget velit</li><li>Eu mauris sollicitudin</li><li>Luctus vel in orci</li><li>Etiam imperdiet</li><li>Rhoncus fermentum</li></ul></div>
  <div class="abs foot-col" style="left:737px"><h4>SUPPORT</h4><ul><li>Aenean eget velit</li><li>Eu mauris sollicitudin</li><li>Luctus vel in orci</li><li>Etiam imperdiet</li><li>Rhoncus fermentum</li></ul></div>
  <div class="abs foot-col" style="left:960px"><h4>CONTACT</h4><ul><li>Customer Service:</li><li>123-456-7890</li><li>info@briskmorningrambles.example</li></ul>
    <div class="social"><span aria-label="Social link"></span><span aria-label="Social link"></span></div>
  </div>
  <div class="abs legal">Copyright © 2019. Company Name. All Right Reserved</div>
</footer>

</body>
</html>
```